"The Orginal LoopPeg's" needs a Package Design!! Everybody's got a LoopPeg, What's Yours?

I need eye popping packaging design!! My LoopPeg's are gonna be big! I'm a single mom I'm based in AZ, so this is big for me. The LoopPeg's keep towels off the floor & so much more!! Color cardboard insert background, bright yellow and Bright blue, like a caribbean blue, funky font for the Product Name. The Original, can be smaller and in an easy script. I have some pictures so you can get an concept and basic design ideas. There are no limits to their uses!! Please call me for any questions or direction.
Updates

I want to thank you all for participating, You each brought a different perspective and had some really good ideas. I will definitely us this service again! Thank you, Dolores Fitzwick

Target Market(s)

Mom's, woman, men, students you name it!!

Colors
fbee3e
0293ce

Requirements
Must have
• Clear pvc packaging so you can see the product and they have to hang over so you see how they are used. The look needs to draw people in to it!! Read my instructions on the downloaded pics and info and if you have questions please let me know. The towel and towel bar can be like a drawing not actual towel picture. On the reverse side is a list of ideas and my website. Other colors for lettering aside from the Caribbean blue for the word "LoopPeg's" is up to you, use your expertise.
Should not have
• The blue is not on the color wheel that is shown here.

```html
<!DOCTYPE html>
<html lang="en">
<head>
<meta charset="utf-8">
<title>The Original LoopPeg's – Package Insert</title>
<link rel="stylesheet" href="https://fonts.googleapis.com/css2?family=Fredoka:wght@500;600;700&family=Luckiest+Guy&display=swap">
<style>
  :root {
    --yellow: #fbee3e;
    --yellow-light: #fff9a8;
    --blue: #0293ce;
    --blue-dark: #0179ad;
    --red: #e3131b;
    --maroon: #a3123a;
    --white: #ffffff;
    --stage: #e9e6e1;
    --photo-skin: #c9b39b;
    --photo-steel: #c4c8cc;
    --photo-green: #cfe59a;
    --photo-wood: #8a6a4c;
  }
  * { box-sizing: border-box; margin: 0; padding: 0; }
  html, body { width: 1200px; height: 796px; overflow: hidden; }
  body {
    background: var(--stage);
    position: relative;
    font-family: "Fredoka", sans-serif;
  }
  .card {
    position: absolute;
    background: radial-gradient(ellipse at 50% 50%, var(--yellow-light) 0%, var(--yellow) 65%);
    box-shadow: 0 6px 18px rgba(0,0,0,.25);
  }
  .card--front { left: 24px; top: 100px; width: 564px; height: 658px; }
  .card--back { left: 608px; top: 66px; width: 548px; height: 655px; }

  /* Front */
  .brand { position: absolute; left: 0; right: 0; top: 40px; text-align: center; }
  .brand__tagline { font-size: 23px; font-weight: 600; color: var(--maroon); line-height: 1; }
  .brand__name {
    display: inline-flex; align-items: center; gap: 10px;
    font-size: 74px; font-weight: 700; color: var(--blue); line-height: 1; margin-top: 2px;
  }
  .brand__dot { width: 22px; height: 22px; border-radius: 50%; background: var(--maroon); }
  .band {
    position: absolute; left: 0; right: 0; top: 160px; height: 74px;
    background: var(--blue);
    border-top: 4px solid var(--white); border-bottom: 4px solid var(--white);
    color: var(--white); text-align: center;
    font-size: 19px; font-weight: 500; line-height: 26px; padding-top: 7px;
  }
  .product {
    position: absolute; left: 138px; top: 254px; width: 276px; height: 192px;
    border: 8px solid var(--blue); border-radius: 10px; background: var(--white);
    padding: 6px;
  }
  .product__image {
    width: 100%; height: 100%; border-radius: 3px;
    background: linear-gradient(90deg, #2a8fc9 0 25%, #b5165a 25% 50%, #ee2a73 50% 75%, #5fbf3a 75%);
  }
  .slogan {
    position: absolute; left: 42px; top: 474px; width: 468px; height: 92px;
    background: var(--blue); border: 5px solid var(--white);
    box-shadow: 0 3px 6px rgba(0,0,0,.25);
    color: var(--white); text-align: center;
    font-family: "Luckiest Guy", sans-serif; font-size: 29px; line-height: 34px;
    padding-top: 10px; letter-spacing: .5px;
  }
  .badge {
    position: absolute; left: 446px; top: 520px; width: 82px; height: 82px;
    border-radius: 50%; background: var(--blue); border: 4px solid var(--white);
    color: var(--white); text-align: center;
    font-size: 11px; font-weight: 600; line-height: 14px;
    display: flex; flex-direction: column; justify-content: center;
  }
  .note {
    position: absolute; left: 0; width: 528px; top: 588px; text-align: center;
    color: var(--maroon); font-size: 14px; font-weight: 600;
  }

  /* Back */
  .headline {
    position: absolute; left: 0; right: 0; top: 58px; text-align: center;
    color: var(--blue); font-size: 16px; font-weight: 700; line-height: 22px; letter-spacing: .6px;
    text-transform: uppercase;
  }
  .headline__accent { color: var(--red); font-size: 20px; }
  .gallery { position: absolute; top: 136px; left: 36px; display: flex; gap: 8px; }
  .gallery__item {
    width: 112px; height: 124px; border: 6px solid var(--blue); border-radius: 10px;
    background: var(--white); padding: 3px;
  }
  .gallery__photo { width: 100%; height: 100%; border-radius: 3px; }
  .gallery__photo--bib { background: linear-gradient(var(--photo-skin), #7fb5d6); }
  .gallery__photo--bar { background: linear-gradient(var(--white), #f1e4e4 60%, #c2203a); }
  .gallery__photo--wrap { background: linear-gradient(var(--white), var(--photo-green)); }
  .gallery__photo--shade { background: linear-gradient(var(--photo-wood) 40%, #d9e8f0 40%); }
  .uses {
    position: absolute; top: 282px; list-style: none;
    color: var(--blue); font-size: 15.5px; font-weight: 600; line-height: 21.4px;
  }
  .uses--left { left: 56px; }
  .uses--right { left: 282px; }
  .uses li { display: flex; align-items: center; gap: 8px; }
  .uses svg { flex: none; }
  .closing {
    position: absolute; left: 0; right: 0; top: 544px; text-align: center;
    color: var(--red); font-size: 21px; font-weight: 700; letter-spacing: 1px;
  }
  .website {
    position: absolute; left: 0; right: 0; top: 578px; text-align: center;
    color: var(--red); font-size: 14px; font-weight: 600;
  }
</style>
</head>
<body>
<svg width="0" height="0" style="position:absolute">
  <symbol id="tick" viewBox="0 0 14 14">
    <rect width="14" height="14" rx="2" fill="#0293ce"/>
    <path d="M3 7.5l2.6 2.6L11 4" fill="none" stroke="#fff" stroke-width="2" stroke-linecap="round" stroke-linejoin="round"/>
  </symbol>
</svg>

<section class="card card--front">
  <div class="brand">
    <div class="brand__tagline">The Original</div>
    <div class="brand__name"><span class="brand__dot"></span>LoopPeg's</div>
  </div>
  <div class="band">NO MORE TOWELS ON THE FLOOR<br>&amp; SO MUCH MORE!!!</div>
  <div class="product">
    <div class="product__image" role="img" aria-label="Four fabric straps with round clips in blue, magenta, pink and green"></div>
  </div>
  <div class="slogan">Everybody's got a LoopPeg<br>What's yours?</div>
  <div class="badge"><span>4 LOOPPEGS</span><span>per box</span></div>
  <p class="note">Thin clear rubber band to hold product in place.</p>
</section>

<section class="card card--back">
  <p class="headline">
    <span class="headline__accent">Endless uses</span> – post a picture of your<br>
    LoopPeg idea to our website and you could win<br>
    a <span class="headline__accent">free</span> package of limited edition LoopPeg's!!
  </p>
  <div class="gallery">
    <div class="gallery__item"><div class="gallery__photo gallery__photo--bib" role="img" aria-label="Toddler wearing a towel clipped as a bib"></div></div>
    <div class="gallery__item"><div class="gallery__photo gallery__photo--bar" role="img" aria-label="Red towel hanging from a towel bar"></div></div>
    <div class="gallery__item"><div class="gallery__photo gallery__photo--wrap" role="img" aria-label="Green towel clipped as a body wrap"></div></div>
    <div class="gallery__item"><div class="gallery__photo gallery__photo--shade" role="img" aria-label="Clip holding a window shade pull down"></div></div>
  </div>
  <ul class="uses uses--left">
    <li><svg width="14" height="14"><use href="#tick"/></svg>Baby Bibs</li>
    <li><svg width="14" height="14"><use href="#tick"/></svg>Baby Strollers</li>
    <li><svg width="14" height="14"><use href="#tick"/></svg>Hanging Bathing Suits</li>
    <li><svg width="14" height="14"><use href="#tick"/></svg>By the Pool</li>
    <li><svg width="14" height="14"><use href="#tick"/></svg>Pull downs for Shades</li>
    <li><svg width="14" height="14"><use href="#tick"/></svg>Tarp Holders</li>
    <li><svg width="14" height="14"><use href="#tick"/></svg>Camping</li>
    <li><svg width="14" height="14"><use href="#tick"/></svg>Room Dividers</li>
    <li><svg width="14" height="14"><use href="#tick"/></svg>College Dorms</li>
    <li><svg width="14" height="14"><use href="#tick"/></svg>The Gym</li>
    <li><svg width="14" height="14"><use href="#tick"/></svg>Photography Backdrops</li>
    <li><svg width="14" height="14"><use href="#tick"/></svg>Traveling</li>
  </ul>
  <ul class="uses uses--right">
    <li><svg width="14" height="14"><use href="#tick"/></svg>Towel wraps</li>
    <li><svg width="14" height="14"><use href="#tick"/></svg>Pet Training</li>
    <li><svg width="14" height="14"><use href="#tick"/></svg>Drying Lingerie</li>
    <li><svg width="14" height="14"><use href="#tick"/></svg>Tablecloths</li>
    <li><svg width="14" height="14"><use href="#tick"/></svg>Dishtowels</li>
    <li><svg width="14" height="14"><use href="#tick"/></svg>The Garage</li>
    <li><svg width="14" height="14"><use href="#tick"/></svg>Hanging Quilts</li>
    <li><svg width="14" height="14"><use href="#tick"/></svg>To hold your pants closed</li>
    <li><svg width="14" height="14"><use href="#tick"/></svg>Curtains (no sewing!)</li>
    <li><svg width="14" height="14"><use href="#tick"/></svg>Valences (no sewing!)</li>
    <li><svg width="14" height="14"><use href="#tick"/></svg>Drapes (no sewing!)</li>
    <li><svg width="14" height="14"><use href="#tick"/></svg>Shower Curtains</li>
  </ul>
  <p class="closing">THE ONLY LIMIT IS YOUR IMAGINATION</p>
  <p class="website">The original LoopPeg's.com</p>
</section>
</body>
</html>
```